VENTURE CAPITAL GROUP BUSINESS CARD DESIGN

Venture Capital Group based in SF looking for a bold business card design. No trendy colour explosion, 3D effects etc. Just "simple" optical effects. Works on your brain, keeps your eye focused and sticks to your mind.
Target Market(s)
Technology startups
Industry/Entity Type
Venture Capital
Contact Information for Business Card
DESMOND WHITLAKE
MANAGING PARTNER
187 FENWORTH ST SAN FRANCISCO, CA 94187
415.555.0142 O
415.555.0147 F
415.555.0193 C
desmond@veldtmoorcapital.ventures

```html
<!DOCTYPE html>
<html lang="en">
<head>
<meta charset="utf-8">
<title>Veldtmoor Capital Group — Business Card</title>
<link rel="stylesheet" href="https://fonts.googleapis.com/css2?family=Cinzel:wght@400&family=EB+Garamond:wght@400;600&display=swap">
<style>
  :root {
    --stage: #e9e8e4;
    --card-dark: #2a2e2b;
    --card-dark-deep: #1c1f1d;
    --card-dark-light: #3a3f3b;
    --card-light: #fbfbfa;
    --green: #1f9a3e;
    --green-bright: #2fb34c;
    --ink: #5b5f5c;
    --ink-soft: #a9adaa;
  }
  * { box-sizing: border-box; margin: 0; padding: 0; }
  html, body { width: 1200px; height: 485px; overflow: hidden; }
  body {
    background: var(--stage);
    display: flex;
    align-items: center;
    justify-content: center;
    gap: 50px;
    font-family: "EB Garamond", Georgia, serif;
  }
  .card {
    position: relative;
    width: 525px;
    height: 300px;
    border-radius: 3px;
    box-shadow: 0 6px 18px rgba(0,0,0,.18);
    overflow: hidden;
  }

  /* Front */
  .card--front { background: var(--card-dark); }
  .card__facets {
    position: absolute; inset: 0;
    background: linear-gradient(135deg, var(--card-dark-light) 0%, var(--card-dark) 45%, var(--card-dark-deep) 100%);
  }
  .brand {
    position: absolute; inset: 0;
    display: flex; align-items: center; justify-content: center; gap: 18px;
  }
  .brand__dot {
    flex: none;
    width: 30px; height: 30px; border-radius: 50%;
    background: var(--green);
  }
  .brand__text { display: flex; flex-direction: column; align-items: flex-end; }
  .brand__name {
    font-family: "Cinzel", "Times New Roman", serif;
    font-size: 40px;
    letter-spacing: 1px;
    line-height: 1;
    color: var(--green-bright);
    white-space: nowrap;
  }
  .brand__sub {
    font-family: "Cinzel", "Times New Roman", serif;
    font-size: 11px;
    letter-spacing: 5px;
    color: var(--ink-soft);
    margin-top: 6px;
    white-space: nowrap;
  }

  /* Back */
  .card--back { background: var(--card-light); }
  .card__brand {
    position: absolute; top: 44px; left: 0; right: 0;
    display: flex; align-items: center; justify-content: center; gap: 10px;
    font-family: "Cinzel", "Times New Roman", serif;
    font-size: 17px;
    letter-spacing: 1.5px;
    color: var(--green);
    white-space: nowrap;
  }
  .card__brand-dot {
    flex: none; width: 16px; height: 16px; border-radius: 50%; background: var(--green);
  }
  .holder { position: absolute; left: 34px; top: 128px; }
  .holder__name {
    font-size: 21px;
    font-variant: small-caps;
    letter-spacing: 1px;
    color: var(--green);
    line-height: 1;
    white-space: nowrap;
  }
  .holder__title { font-size: 11px; color: var(--ink); margin-top: 5px; }

  .contacts {
    position: absolute; left: 34px; top: 196px;
    list-style: none;
    display: flex; flex-direction: column; gap: 5px;
  }
  .contacts__item {
    display: flex; align-items: center; gap: 8px;
    font-size: 11px; color: var(--ink); line-height: 1;
    white-space: nowrap;
  }
  .contacts__icon { width: 13px; height: 13px; flex: none; }
  .contacts__item--address {
    color: var(--green); font-weight: 600; font-size: 11.5px;
  }
</style>
</head>
<body>

<section class="card card--front" aria-label="Card front">
  <div class="card__facets" role="img" aria-label="Dark faceted polygon texture"></div>
  <div class="brand">
    <span class="brand__dot"></span>
    <div class="brand__text">
      <span class="brand__name">VELDTMOOR</span>
      <span class="brand__sub">CAPITAL GROUP</span>
    </div>
  </div>
</section>

<section class="card card--back" aria-label="Card back">
  <div class="card__brand"><span class="card__brand-dot"></span>VELDTMOOR CAPITAL GROUP</div>

  <div class="holder">
    <div class="holder__name">Desmond Whitlake</div>
    <div class="holder__title">Founder/ Owner</div>
  </div>

  <ul class="contacts">
    <li class="contacts__item">
      <svg class="contacts__icon" viewBox="0 0 16 16" aria-hidden="true"><circle cx="8" cy="8" r="8" fill="var(--green)"/><rect x="4.5" y="4" width="7" height="8" fill="#fff"/><rect x="6" y="5.5" width="1.4" height="1.4" fill="var(--green)"/><rect x="8.6" y="5.5" width="1.4" height="1.4" fill="var(--green)"/><rect x="7.2" y="9" width="1.6" height="3" fill="var(--green)"/></svg>
      415.555.0142
    </li>
    <li class="contacts__item">
      <svg class="contacts__icon" viewBox="0 0 16 16" aria-hidden="true"><circle cx="8" cy="8" r="8" fill="var(--green)"/><rect x="5.5" y="3.8" width="5" height="3" fill="#fff"/><rect x="3.8" y="6.8" width="8.4" height="4" rx="1" fill="#fff"/><rect x="5.5" y="9.5" width="5" height="3" fill="#fff" stroke="var(--green)" stroke-width=".6"/></svg>
      415.555.0147
    </li>
    <li class="contacts__item">
      <svg class="contacts__icon" viewBox="0 0 16 16" aria-hidden="true"><circle cx="8" cy="8" r="8" fill="var(--green)"/><path d="M5.2 4.2l1.6-.4.9 2.1-1 .8c.5 1.1 1.3 1.9 2.4 2.4l.8-1 2.1.9-.4 1.6c-3.4.3-6.7-3-6.4-6.4z" fill="#fff"/></svg>
      415.555.0193
    </li>
    <li class="contacts__item">
      <svg class="contacts__icon" viewBox="0 0 16 16" aria-hidden="true"><circle cx="8" cy="8" r="8" fill="var(--green)"/><rect x="4" y="5" width="8" height="6" fill="#fff"/><path d="M4 5l4 3.3L12 5" fill="none" stroke="var(--green)" stroke-width=".8"/></svg>
      desmond@veldtmoorcapital.ventures
    </li>
    <li class="contacts__item contacts__item--address">187 Fenworth St San Francisco, CA 94187</li>
  </ul>
</section>

</body>
</html>
```